3 Page Design for Ninth Bay Capital

We want a Home Page, About Page, and Products & Services Page for Ninth Bay Capital. Please refer to the attached docs for more info.
If done in Figma, would like Figma files that can easily be ported to Wordpress.

```html
<!DOCTYPE html>
<html lang="en">
<head>
<meta charset="utf-8">
<title>Ninth Bay Capital — Home</title>
<link href="https://fonts.googleapis.com/css2?family=Inter:wght@400;500;600;700;800&display=swap" rel="stylesheet">
<style>
:root{
  --beige:#e8dcc8;
  --beige-deep:#dccdb4;
  --maroon:#9b1c2e;
  --brown:#8a6f4e;
  --ink:#2b2b2b;
  --dark:#3a3a3c;
  --white:#ffffff;
  --muted:#6b6b6b;
}
*{margin:0;padding:0;box-sizing:border-box}
html,body{width:1200px;height:3391px;overflow:hidden}
body{position:relative;background:var(--white);font-family:'Inter',sans-serif;color:var(--ink)}
.abs{position:absolute}
.btn{position:absolute;background:var(--maroon);color:var(--white);font-weight:700;font-size:15px;display:flex;align-items:center;justify-content:center;border-radius:3px;text-decoration:none}
.rule{position:absolute;height:3px;background:var(--ink)}
.photo{position:absolute;border-radius:3px}
/* header */
.site-header{position:absolute;left:0;top:0;width:1200px;height:80px;background:var(--white);z-index:5}
.brand{position:absolute;left:116px;top:14px;width:246px;height:122px;background:var(--white);border-radius:6px;box-shadow:0 2px 10px rgba(0,0,0,.12);display:flex;flex-direction:column;align-items:center;justify-content:center;gap:10px;z-index:6}
.brand-dot{width:44px;height:44px;border-radius:50%;background:var(--brown)}
.brand-name{font-weight:700;font-size:19px;color:var(--ink);letter-spacing:.3px}
.nav a{position:absolute;top:30px;font-size:14px;color:var(--ink);text-decoration:none}
.nav a.active{font-weight:700}
/* hero */
.hero-title{left:120px;top:202px;font-size:68px;font-weight:800;letter-spacing:-1px;color:var(--ink)}
.hero-sub{left:120px;top:284px;font-size:41px;font-weight:700;color:#8c8378}
.hero-text{left:120px;top:352px;font-size:18.5px;line-height:28px;font-weight:500;width:460px}
/* mission */
.mission-title{left:641px;top:758px;font-size:37px;font-weight:600}
.mission-lead{left:643px;top:845px;font-size:21.5px;line-height:28px;font-weight:600;color:var(--brown);width:400px}
.mission-text{left:643px;top:915px;width:390px;font-size:14px;line-height:24px;text-align:justify}
/* high design */
.center{left:0;width:1200px;text-align:center}
.hd-title{top:1375px;font-size:38px;font-weight:500}
.hd-title b{font-weight:700}
.hd-text{top:1490px;font-size:14px;line-height:24px}
.card-label{position:absolute;background:#2e2a28;color:var(--white);font-weight:700;font-size:18px;display:flex;align-items:center;padding-left:30px;border-radius:0 22px 22px 0}
.card-panel{position:absolute;left:120px;top:1682px;width:296px;height:184px;background:rgba(112,84,160,.85);border-radius:0 10px 10px 0;color:var(--white);padding:26px 30px}
.card-panel h3{font-size:18px;font-weight:600;margin-bottom:14px}
.card-panel p{font-size:13.5px;line-height:24px}
.dot{position:absolute;top:1922px;width:14px;height:14px;border-radius:50%;background:#cfcfcf}
/* system */
.sys-title{top:2096px;font-size:38px;font-weight:600;line-height:48px;color:var(--white)}
.sys-text{top:2240px;font-size:14px;line-height:24px;color:var(--white)}
.step{position:absolute;top:2340px;width:220px;text-align:center;color:var(--white)}
.step-ring{position:absolute;width:118px;height:118px;border-radius:50%;background:var(--beige);border:6px solid var(--beige)}
.step-core{position:absolute;left:8px;top:8px;width:90px;height:90px;border-radius:50%;background:var(--brown)}
.step-num{position:absolute;width:52px;height:52px;border-radius:50%;background:#9d9d9d;color:var(--white);font-size:27px;font-weight:700;display:flex;align-items:center;justify-content:center;border:3px solid #e4e4e4}
.step h4{position:absolute;top:130px;left:0;width:220px;font-size:18px;line-height:24px;font-weight:700}
.step p{position:absolute;top:192px;left:0;width:220px;font-size:13.5px;line-height:24px}
/* cta */
.cta-title{left:117px;top:2805px;font-size:38px;font-weight:500}
.cta-title b{font-weight:700}
.cta-sub{left:121px;top:2908px;font-size:22px;color:#3d3d3d}
/* footer */
.f-brand{left:128px;top:3130px;display:flex;align-items:center;gap:10px}
.f-head{top:3102px;font-size:18px;font-weight:500;letter-spacing:.3px}
.f-link{left:414px;font-size:14.5px;color:#555;display:flex;align-items:center;gap:8px}
.f-contact{left:645px;font-size:14.5px;color:#555;line-height:25px}
.f-icon{position:absolute;left:604px;width:28px;height:28px;border-radius:50%;background:var(--maroon);display:flex;align-items:center;justify-content:center}
.f-news{left:877px;top:3140px;width:200px;font-size:12px;line-height:24px;color:#555}
.f-input{left:879px;top:3208px;width:200px;height:42px;border:1px solid #ddd;border-radius:4px;font-size:12px;color:#777;padding-left:14px;display:flex;align-items:center}
.f-send{position:absolute;right:3px;top:4px;width:38px;height:32px;border-radius:4px;background:var(--maroon);display:flex;align-items:center;justify-content:center}
.copy{top:3358px;font-size:13px;color:#333}
</style>
</head>
<body>

<!-- background bands -->
<svg class="abs" style="left:0;top:0" width="1200" height="3391" aria-hidden="true">
  <path d="M0 80 H1200 V1198 Q600 1370 0 1198 Z" fill="var(--beige)"/>
  <path d="M0 2004 H1200 V2803 Q600 2620 0 2803 Z" fill="var(--dark)"/>
  <path d="M0 2803 Q600 2620 1200 2803 V2954 Q600 3110 0 2954 Z" fill="var(--beige)"/>
</svg>

<!-- header -->
<header class="site-header">
  <nav class="nav">
    <a class="active" style="left:390px" href="#">HOME</a>
    <a style="left:461px" href="#">ABOUT</a>
    <a style="left:538px" href="#">PRODUCTS</a>
    <a style="left:642px" href="#">SERVICES</a>
    <a style="left:737px" href="#">CONTACT US</a>
  </nav>
  <a class="btn" style="left:854px;top:20px;width:225px;height:39px" href="#">Start Your Transition</a>
</header>
<div class="brand"><span class="brand-dot"></span><span class="brand-name">NINTH BAY CAPITAL</span></div>

<!-- hero -->
<svg class="abs" style="left:0;top:80px" width="1200" height="580" role="img" aria-label="Professional woman holding a tablet in a bright office">
  <defs><linearGradient id="heroG" x1="0" y1="0" x2="1" y2="1"><stop offset="0" stop-color="#c9c2b6"/><stop offset=".55" stop-color="#5d7ea3"/><stop offset="1" stop-color="#2f4f78"/></linearGradient></defs>
  <path d="M737 0 H1200 V460 Q900 520 540 571 Z" fill="url(#heroG)"/>
</svg>
<h1 class="abs hero-title">Built for Legacy.</h1>
<h2 class="abs hero-sub">Designed for Performance.</h2>
<p class="abs hero-text">Systems, strategy, and structure for athletes and entrepreneurs building long-term success.</p>
<a class="btn" style="left:120px;top:433px;width:138px;height:39px" href="#">Get Started</a>

<!-- mission -->
<div class="photo" style="left:147px;top:734px;width:213px;height:207px;background:linear-gradient(160deg,#dfe3e8,#b7a08c)" role="img" aria-label="Coach speaking to a seated audience"></div>
<div class="photo" style="left:373px;top:749px;width:214px;height:206px;background:linear-gradient(160deg,#8d8270,#c8c0b2)" role="img" aria-label="Businesswoman presenting to colleagues"></div>
<div class="photo" style="left:147px;top:955px;width:213px;height:207px;background:linear-gradient(160deg,#56534f,#a09590)" role="img" aria-label="Group exercising in a gym"></div>
<div class="photo" style="left:373px;top:970px;width:214px;height:206px;background:linear-gradient(160deg,#4a5260,#9aa38c)" role="img" aria-label="Runners racing on a road"></div>
<div class="abs" style="left:300px;top:881px;width:132px;height:132px;border-radius:50%;background:var(--white);box-shadow:0 2px 10px rgba(0,0,0,.2)"></div>
<h2 class="abs mission-title">Our Mission</h2>
<div class="rule" style="left:643px;top:818px;width:57px"></div>
<p class="abs mission-lead">Helping You Build a Life That Performs Beyond the Game.</p>
<p class="abs mission-text">Northbay supports developing athletes and driven entrepreneurs with tools that redefine how you manage performance, wealth, and wellness.<br>Our mission is simple&nbsp; create structure where there is overwhelm, clarity where there is noise, and a long-term path where most systems stop short.</p>
<a class="btn" style="left:645px;top:1088px;width:138px;height:40px" href="#">Read More</a>

<!-- high design -->
<h2 class="abs center hd-title">Where High Performance Meets <b>High Design.</b></h2>
<div class="rule" style="left:569px;top:1448px;width:56px"></div>
<p class="abs center hd-text">Success today demands more than talent. It requires a refined approach — one that merges technical precision with<br>long-term thinking.<br>Our visual and strategic framework reflects that blend: quiet confidence, intentional motion, and architectural balance.</p>

<div class="photo" style="left:120px;top:1599px;width:348px;height:280px;background:linear-gradient(180deg,#7d8a9c,#b5aa9a 60%,#3e6b8f)" role="img" aria-label="Athlete celebrating in a stadium"></div>
<div class="card-panel"><h3>Athletes</h3><p>Lorem Ipsum is simply dummy text of the printing and typesetting industry. Lorem Ipsum has been the industry's standard dummy</p></div>
<div class="photo" style="left:501px;top:1599px;width:349px;height:280px;background:radial-gradient(circle at 50% 40%,#8a5a3e,#2a1a14 75%)" role="img" aria-label="Boxer in a ring"></div>
<div class="card-label" style="left:501px;top:1800px;width:148px;height:45px">Boxer</div>
<div class="photo" style="left:883px;top:1599px;width:317px;height:280px;border-radius:3px 0 0 3px;background:linear-gradient(160deg,#9aa3ad,#d8d2c8 55%,#e59433)" role="img" aria-label="Entrepreneurs reviewing documents in an office"></div>
<div class="card-label" style="left:883px;top:1800px;width:148px;height:45px">Entrepreneur</div>
<span class="dot" style="left:568px;background:#111"></span>
<span class="dot" style="left:592px"></span>
<span class="dot" style="left:615px"></span>

<!-- system -->
<h2 class="abs center sys-title">A Build-Once System for<br>Lifelong Performance.</h2>
<div class="rule" style="left:572px;top:2214px;width:56px;background:var(--white)"></div>
<p class="abs center sys-text">Our approach is engineered to move you from uncertainty to clarity — with a structure that supports both the athlete you<br>are today and the entrepreneur you’re becoming.</p>

<div class="step" style="left:133px">
  <div class="step-ring" style="left:51px;top:0"><div class="step-core"></div></div>
  <div class="step-num" style="left:52px;top:-33px">01</div>
  <h4>Performance<br>Discipline</h4>
  <p>Daily protocols that strengthen mindset, habits, and identity.</p>
</div>
<div class="step" style="left:370px">
  <div class="step-ring" style="left:51px;top:0"><div class="step-core"></div></div>
  <div class="step-num" style="left:52px;top:-33px">02</div>
  <h4>Business<br>Foundations</h4>
  <p>Clear financial, operational, and branding systems to grow your career off the field.</p>
</div>
<div class="step" style="left:607px">
  <div class="step-ring" style="left:51px;top:0"><div class="step-core"></div></div>
  <div class="step-num" style="left:52px;top:-33px">03</div>
  <h4>Wealth &amp; Risk<br>Strategy</h4>
  <p>A roadmap for long-term financial stability and generational success.</p>
</div>
<div class="step" style="left:845px">
  <div class="step-ring" style="left:51px;top:0"><div class="step-core"></div></div>
  <div class="step-num" style="left:52px;top:-33px">04</div>
  <h4>Automation &amp;<br>Tools</h4>
  <p>AI-assisted systems that reduce friction and keep you consistent.</p>
</div>
<svg class="abs" style="left:0;top:2380px" width="1200" height="60" aria-hidden="true" fill="none" stroke="#fff" stroke-width="2">
  <path d="M322 38 Q355 50 392 30"/><path d="M382 26 L393 30 L386 40"/>
  <path d="M565 20 Q600 5 636 24"/><path d="M626 17 L637 24 L628 32"/>
  <path d="M808 35 Q845 48 880 30"/><path d="M870 26 L881 30 L874 40"/>
</svg>

<!-- cta -->
<h2 class="abs cta-title">Build Your Next Chapter <b>with Precision.</b></h2>
<div class="rule" style="left:121px;top:2874px;width:55px"></div>
<p class="abs cta-sub">Success doesn’t happen by accident — it happens by system.</p>
<a class="btn" style="left:891px;top:2846px;width:188px;height:40px" href="#">Start Your Transition</a>

<!-- footer -->
<div class="abs f-brand"><span class="brand-dot"></span><span class="brand-name">NINTH BAY CAPITAL</span></div>
<h3 class="abs f-head" style="left:414px">MAIN LINKS</h3>
<a class="abs f-link" style="top:3139px">➔ Home</a>
<a class="abs f-link" style="top:3171px">➔ Services</a>
<a class="abs f-link" style="top:3203px">➔ Product</a>
<a class="abs f-link" style="top:3235px">➔ Contact Us</a>

<h3 class="abs f-head" style="left:607px">CONTACT US</h3>
<span class="f-icon" style="top:3146px"><svg width="14" height="16" viewBox="0 0 14 16"><path d="M7 1a5 5 0 0 0-5 5c0 4 5 9 5 9s5-5 5-9a5 5 0 0 0-5-5z" fill="#fff"/><circle cx="7" cy="6" r="2" fill="#9b1c2e"/></svg></span>
<p class="abs f-contact" style="top:3148px">Ninth Bay Capital,<br>Lakeview 40217</p>
<span class="f-icon" style="top:3208px"><svg width="14" height="14" viewBox="0 0 14 14"><path d="M3 1l2 3-1.5 1.5a8 8 0 0 0 5 5L10 9l3 2-1.5 2.5C6 13 1 8 .5 2.5z" fill="#fff"/></svg></span>
<p class="abs f-contact" style="top:3209px">+1 555 010 2040</p>
<span class="f-icon" style="top:3256px"><svg width="14" height="11" viewBox="0 0 14 11"><rect width="14" height="11" rx="1.5" fill="#fff"/><path d="M1 1.5l6 4.5 6-4.5" stroke="#9b1c2e" stroke-width="1.4" fill="none"/></svg></span>
<p class="abs f-contact" style="top:3257px">info@ninthbaycapital.example</p>

<h3 class="abs f-head" style="left:874px">NEWSLETTER SIGN UP</h3>
<p class="abs f-news">We Will Notify You Of Any Important News</p>
<div class="abs f-input">Your Email Address
  <span class="f-send"><svg width="20" height="20" viewBox="0 0 20 20" fill="none" stroke="#fff" stroke-width="1.5"><path d="M2 9l16-7-6 16-3-7z"/><path d="M9 11l9-9"/></svg></span>
</div>

<div class="abs" style="left:118px;top:3327px;width:961px;height:1px;background:#333"></div>
<p class="abs center copy">© 2025 Ninth Bay Capital I All Rights Reserved</p>

</body>
</html>
```